Business Card Design Project

Basic business card with minimal details. I just need company name, email & web address, telephone and my name.
I would like the back of the card to be grey with my logo & company name centred.

Target Market(s)

Architects
Builders
Property Developers

Industry/Entity Type

Business

Font styles to use
Sans Serif

Colors

Designer to choose colors to be used in the design.

Requirements
Must have
• Tallow Crest
Rupert Hazelby - Director
M: 0427 915203
E: rupert@tallowcrest.com.au
W: www.tallowcrest.com.au
Should not have
• No other images or pictures

```html
<!DOCTYPE html>
<html lang="en">
<head>
<meta charset="utf-8">
<title>Tallow Crest – Business Card</title>
<link rel="stylesheet" href="https://fonts.googleapis.com/css2?family=Arimo:wght@400;700&family=Ubuntu:wght@500;700&display=swap">
<style>
  :root {
    --backdrop: #ecebe8;
    --card: #ffffff;
    --card-back: #d5d8db;
    --ink: #111111;
    --accent: #b3232b;
    --brand-red: #a6163a;
    --slate: #3f4b57;
  }
  html, body {
    margin: 0;
    padding: 0;
    width: 1200px;
    height: 1200px;
    overflow: hidden;
    background: var(--backdrop);
  }
  .canvas {
    position: relative;
    width: 1200px;
    height: 1200px;
  }
  .card {
    position: absolute;
    left: 140px;
    width: 928px;
    height: 572px;
    background: var(--card);
    box-shadow: 0 2px 8px rgba(0, 0, 0, 0.18);
  }
  .card--front { top: 14px; }
  .card--back {
    top: 604px;
    background: var(--card-back);
  }

  .identity {
    position: absolute;
    left: 581px;
    top: 101px;
  }
  .identity__name {
    margin: 0;
    font-family: "Ubuntu", "Arimo", sans-serif;
    font-weight: 700;
    font-size: 30px;
    line-height: 1;
    color: var(--ink);
    word-spacing: 3px;
  }
  .identity__role {
    margin: 7px 0 0;
    font-family: "Ubuntu", "Arimo", sans-serif;
    font-weight: 500;
    font-size: 28px;
    line-height: 1;
    color: var(--accent);
  }

  .contact {
    position: absolute;
    left: 78px;
    top: 402px;
    margin: 0;
    padding: 0;
    list-style: none;
    font-family: "Arimo", sans-serif;
    font-size: 28px;
    color: var(--ink);
  }
  .contact__item {
    height: 42px;
    line-height: 32px;
  }
  .contact__label { font-weight: 700; }

  .brand {
    position: absolute;
    left: 0;
    right: 0;
    top: 360px;
    display: flex;
    align-items: center;
    justify-content: center;
    gap: 18px;
  }
  .brand__mark {
    width: 32px;
    height: 32px;
    background: var(--brand-red);
  }
  .brand__name {
    font-family: "Arimo", sans-serif;
    font-weight: 400;
    font-size: 44px;
    line-height: 1;
    letter-spacing: 2px;
    color: var(--slate);
    text-transform: uppercase;
  }
</style>
</head>
<body>
<main class="canvas">
  <section class="card card--front">
    <div class="identity">
      <h1 class="identity__name">Rupert Hazelby</h1>
      <p class="identity__role">Director</p>
    </div>
    <ul class="contact">
      <li class="contact__item"><span class="contact__label">Mobile</span> : 0427 915203</li>
      <li class="contact__item"><span class="contact__label">Email</span> : rupert@tallowcrest.com.au</li>
      <li class="contact__item"><span class="contact__label">Web</span> : www.tallowcrest.com.au</li>
    </ul>
  </section>

  <section class="card card--back">
    <div class="brand">
      <span class="brand__mark" aria-hidden="true"></span>
      <span class="brand__name">Tallow Crest</span>
    </div>
  </section>
</main>
</body>
</html>
```